NEW Wordpress Website Design for a Dynamic Long Term Healthcare Company in Hawaii

I would like a new website design for my current company, Marlow Health Collective, which has two different brands - Marlow Homecare and Marlow Senior Living. You can see the current website at www.marlowhealth-example.com. The website should be built using Wordpress Software and the Framewise theme. The website should have a local Hawaii island/tropical feel, but look professional for healthcare. I'm looking for something fresh, and want the designer to select colors, styles, etc.

In the Header, on all pages, I would like a menu that includes Home Care, Senior Living, Rates, and About Us.
Under each of the Header Menu Titles, I would like these drop downs included:
Home Care (drop down pages)- Nurse Aide Care, 24-Hour Home Care, Skilled Nursing, Lifestyle Aide, Hospice at Home, Bathing & Meal Service.
Senior Living (drop down pages) - Long-Term Stay, Short-Term Stay.
Rates (drop down page) - Rates.
About Us (drop down pages) - Our Mission, Ohana Talk, About Dana Marlow.

In the footer, on all pages, you should include the address: 248 Pueo Lane, Suite 310, Honolulu, HI 96817. Phone number: 808-555-0172
The footer should also include buttons for a page called Learn, Caregiver Jobs, and each of the service page links to include: Nurse Aide Care, 24-Hour Home Care, Skilled Nursing, Lifestyle Aide, Hospice at Home, Bathing & Meal Service.
Please don't take the current website and redesign a few aspects. I'm looking for a completely different look and feel.

Target Market(s)

40-80 year olds

Industry/Entity Type

Long Term Healthcare

Coding

Coded - Design and coding required

Requirements
Should not have
• Our existing website as a template. We are looking for a complete redesign. Thank you.

```html
<!DOCTYPE html>
<html lang="en">
<head>
<meta charset="utf-8">
<title>Marlow Health Collective – Homecare &amp; Senior Living</title>
<link href="https://fonts.googleapis.com/css2?family=Cinzel:wght@400;600&family=Montserrat:wght@400;500;600;700&family=Quicksand:wght@400;500;600&display=swap" rel="stylesheet">
<style>
:root{
  --teal:#3ea5ae;
  --teal-dark:#2f8f99;
  --orange:#f5a05a;
  --orange-soft:#f7b67c;
  --cream:#fcf3e9;
  --ink:#222;
  --text:#444;
  --white:#fff;
}
*{box-sizing:border-box;margin:0;padding:0}
html,body{width:1200px;height:4386px;overflow:hidden}
body{position:relative;background:var(--white);font-family:"Quicksand",sans-serif;color:var(--text)}
.abs{position:absolute}
.heading{font-family:"Cinzel",serif;font-weight:400;color:var(--ink);letter-spacing:1px}
.rule{position:absolute;height:2px;width:52px;background:var(--teal)}
.rule::after{content:"";position:absolute;left:10px;top:6px;width:32px;height:2px;background:var(--teal)}
.btn{position:absolute;display:flex;align-items:center;justify-content:center;border-radius:26px;color:var(--white);font-family:"Montserrat",sans-serif;font-weight:600;font-size:14px;letter-spacing:.5px}
.btn-teal{background:var(--teal)}
.btn-orange{background:var(--orange)}
.photo{position:absolute;overflow:hidden}

/* header */
.site-header{position:absolute;left:0;top:0;width:1200px;height:84px;background:var(--white);z-index:3}
.brand{position:absolute;left:115px;top:16px;display:flex;align-items:center;gap:10px}
.brand-mark{width:50px;height:50px;border-radius:50%;background:var(--orange)}
.brand-name{font-family:"Quicksand",sans-serif;font-weight:600;font-size:22px;color:var(--teal-dark);line-height:1.05}
.main-nav{position:absolute;left:390px;top:32px;display:flex;gap:36px;font-family:"Montserrat",sans-serif;font-size:13px;font-weight:500;color:#333}
.main-nav span::after{content:" \2304";color:#999;font-size:11px}
.header-phone{position:absolute;left:927px;top:26px;display:flex;align-items:center;gap:8px;font-family:"Montserrat",sans-serif;font-weight:700;font-size:18px;color:#222}
.phone-dot{width:32px;height:32px;border-radius:50%;background:var(--orange);display:flex;align-items:center;justify-content:center}

/* hero */
.hero-photo{left:0;top:84px;width:1200px;height:650px;background:linear-gradient(90deg,#f9ecdf 0%,#f3dcc2 35%,#c9a37a 60%,#8a6a4a 80%,#a7b77f 100%)}
.hero-badge{left:102px;top:162px;width:426px;height:426px;border-radius:50%;border:2px solid #cde6e6;background:rgba(252,243,233,.82);text-align:center}
.hero-badge .kicker{margin-top:110px;font-family:"Montserrat",sans-serif;font-size:18px;font-weight:500;color:#222;letter-spacing:.5px}
.hero-badge h1{font-family:"Cinzel",serif;font-weight:400;font-size:58px;line-height:60px;margin-top:12px}
.hero-badge h1 .accent{color:var(--orange)}
.hero-badge h1 .dark{color:#111}

/* mission */
.mission-photo{left:94px;top:816px;width:510px;height:408px;border-radius:0 60px 0 60px;background:linear-gradient(135deg,#b88a4a,#d9c27a 40%,#9a4d2e 80%)}
.mission-frame{left:94px;top:830px;width:514px;height:400px;border:6px solid var(--orange);border-radius:0 60px 0 60px;border-top:none;border-right:none}
.mission h2{position:absolute;left:650px;top:856px;font-size:46px}
.body-copy{font-size:17px;line-height:29.5px;color:#444}

/* home care */
.homecare-band{left:0;top:1310px;width:1200px;height:790px;background:var(--teal)}
.homecare h2{position:absolute;left:0;width:1200px;text-align:center;top:1380px;font-size:44px;color:var(--white)}
.service-node{position:absolute;width:74px;height:74px;border-radius:50%;background:var(--orange);border:4px solid #f8c089;display:flex;align-items:center;justify-content:center}
.service-label{position:absolute;font-family:"Montserrat",sans-serif;font-weight:700;font-size:16px;line-height:18px;color:var(--white)}
.service-label.right{text-align:right}

/* senior living */
.senior-bg{left:0;top:2094px;width:1200px;height:600px;background:linear-gradient(180deg,#fdf6ee,#fbefe2)}
.tile-caption{position:absolute;left:18px;bottom:18px;right:14px;display:flex;justify-content:space-between;align-items:center;color:var(--white);font-family:"Montserrat",sans-serif;font-weight:700;font-size:17px}
.tile-arrow{width:30px;height:30px;border-radius:50%;background:var(--orange);display:flex;align-items:center;justify-content:center}
.check-item{position:absolute;left:130px;font-family:"Montserrat",sans-serif;font-weight:600;font-size:18px;color:#333}
.check-item::before{content:"\203A";color:var(--teal);font-size:24px;margin-right:10px;font-weight:700}

/* testimonials */
.testimonial{position:absolute;width:446px;height:258px;border:2px solid var(--teal);border-radius:0 0 30px 0;background:var(--white);padding:30px 50px}
.testimonial p{font-size:16px;line-height:27px;color:#555}
.reviewer{margin-top:12px;font-family:"Montserrat",sans-serif;font-weight:700;font-size:15px;color:#333}
.stars{color:var(--orange);font-size:22px;letter-spacing:4px}
.quote-mark{position:absolute;right:30px;bottom:28px;font-family:"Cinzel",serif;font-size:90px;line-height:60px;color:var(--orange);height:40px}

/* schedule */
.schedule-band{left:0;top:3238px;width:1200px;height:620px;background:linear-gradient(180deg,#f6a55d,#f7b27a 60%,#f9c08e)}
.schedule h2{position:absolute;left:108px;top:3325px;font-size:38px;line-height:44px;color:var(--white)}
.field{position:absolute;height:44px;background:var(--white);border:1px solid #e4c7a9;font-size:14px;color:#555;padding:14px 14px}
.consult-photo{left:650px;top:3288px;width:470px;height:470px;border-radius:50%;border:10px solid #fce7d4;background:linear-gradient(135deg,#c59a5b,#e4cf8b 40%,#a9452e 75%,#d6b27a)}

/* footer */
.footer-col h3{font-family:"Quicksand",sans-serif;font-weight:600;font-size:20px;color:#222;border-left:2px solid var(--orange);padding-left:16px}
.footer-col ul{list-style:none;margin-top:18px;padding-left:18px}
.footer-col li{font-size:15px;line-height:31px;color:#333}
.social{position:absolute;top:4142px;width:26px;height:26px;border-radius:50%;border:2px solid var(--teal)}
.copyright{position:absolute;left:0;width:1200px;top:4271px;text-align:center;font-size:12px;color:#333}
.copyright u{text-decoration:underline}
</style>
</head>
<body>

<!-- header -->
<header class="site-header">
  <div class="brand"><div class="brand-mark"></div><div class="brand-name">Marlow Health<br>Collective</div></div>
  <nav class="main-nav"><span>HOME CARE</span><span>SENIOR LIVING</span><span>RATES</span><span>ABOUT US</span></nav>
  <div class="header-phone"><div class="phone-dot"><svg width="16" height="16" viewBox="0 0 24 24"><path fill="#fff" d="M6.6 10.8a15 15 0 0 0 6.6 6.6l2.2-2.2c.3-.3.7-.4 1-.2 1.1.4 2.3.6 3.6.6.6 0 1 .4 1 1V20c0 .6-.4 1-1 1A17 17 0 0 1 3 4c0-.6.4-1 1-1h3.5c.6 0 1 .4 1 1 0 1.3.2 2.5.6 3.6.1.3 0 .7-.2 1z"/></svg></div>808-555-0172</div>
</header>

<!-- hero -->
<section class="hero">
  <div class="abs hero-photo" role="img" aria-label="Caregiver in blue scrubs chatting with a smiling senior woman on a leather sofa in a bright living room"></div>
  <div class="abs hero-badge">
    <div class="kicker">MARLOW HEALTH COLLECTIVE</div>
    <h1><span class="accent">Homecare &amp;</span><br><span class="dark">Senior Living</span></h1>
    <div class="btn btn-teal" style="left:128px;top:298px;width:174px;height:46px;">VIEW RATES &#8250;</div>
  </div>
  <svg class="abs" style="left:0;top:630px" width="1200" height="130" viewBox="0 0 1200 130" aria-hidden="true">
    <path d="M0 80 C300 10 600 130 1200 20 L1200 130 L0 130Z" fill="#fff"/>
    <path d="M0 98 C250 40 500 60 700 95" stroke="var(--teal)" stroke-width="10" fill="none"/>
    <path d="M380 75 C700 130 950 110 1200 30" stroke="var(--orange)" stroke-width="14" fill="none"/>
  </svg>
</section>

<!-- mission -->
<section class="mission">
  <div class="abs" style="left:0;top:1040px;width:120px;height:200px;background:linear-gradient(160deg,#6c9a3a,#b9d27a);opacity:.5;border-radius:0 100px 0 0" role="img" aria-label="Palm frond accent"></div>
  <div class="abs mission-frame"></div>
  <div class="photo mission-photo" role="img" aria-label="Trainer leading three seniors in a seated dumbbell exercise class"></div>
  <h2 class="heading">Our Mission</h2>
  <div class="rule" style="left:656px;top:922px"></div>
  <p class="abs body-copy" style="left:650px;top:945px;width:520px">At Marlow Health Collective, our mission is to provide compassionate and professional long-term healthcare services that empower individuals to maintain their highest level of independence, health, and well-being in the comfort of their own homes or ours, either through our licensed home healthcare agency</p>
  <div class="btn btn-orange" style="left:646px;top:1146px;width:186px;height:48px;">LEARN MORE &#8250;</div>
</section>

<!-- home care -->
<section class="homecare">
  <div class="abs homecare-band"></div>
  <h2 class="heading">Home Care</h2>
  <div class="rule" style="left:574px;top:1438px;background:#fff"></div>
  <p class="abs" style="left:200px;top:1462px;width:800px;text-align:center;font-size:18px;line-height:23px;color:#fff">Marlow Homecare understands that every person's care journey is unique. We tailor our in-home services to meet the diverse nurturing experience</p>
  <svg class="abs" style="left:0;top:1300px" width="1200" height="800" aria-hidden="true">
    <path d="M288 1040 A300 300 0 0 1 962 1040" transform="translate(0,-700)" stroke="#cfe9eb" stroke-width="3" fill="none"/>
    <path d="M288 340 L288 520 M962 340 L962 520" stroke="#cfe9eb" stroke-width="3" fill="none"/>
  </svg>
  <div class="photo" style="left:357px;top:1606px;width:536px;height:536px;border-radius:50%;border:8px solid #fbd7b2;background:linear-gradient(135deg,#e4d98e,#b9a06a 45%,#2fa3b4 75%,#e8e0cf)" role="img" aria-label="Nurse in teal scrubs helping a senior man button his shirt at his bedside"></div>

  <div class="service-node" style="left:414px;top:1580px"><svg width="34" height="34" viewBox="0 0 24 24" fill="none" stroke="#fff" stroke-width="1.6"><circle cx="12" cy="7" r="3"/><path d="M5 21v-3a7 7 0 0 1 14 0v3M12 13v5M9.5 15.5h5"/></svg></div>
  <div class="service-label right" style="left:290px;top:1590px;width:114px">SKILLED<br>NURSING</div>

  <div class="service-node" style="left:297px;top:1691px"><svg width="34" height="34" viewBox="0 0 24 24" fill="none" stroke="#fff" stroke-width="1.6"><path d="M3 11 12 3l9 8v10H3z"/><circle cx="12" cy="14" r="3.5"/></svg></div>
  <div class="service-label right" style="left:140px;top:1701px;width:140px">24-HOUR<br>HOME CARE</div>

  <div class="service-node" style="left:249px;top:1844px"><svg width="34" height="34" viewBox="0 0 24 24" fill="none" stroke="#fff" stroke-width="1.6"><circle cx="12" cy="8" r="3.5"/><path d="M6 21v-3a6 6 0 0 1 12 0v3M8 4.5h8"/></svg></div>
  <div class="service-label right" style="left:110px;top:1860px;width:128px">NURSE<br>AIDE CARE</div>

  <div class="service-node" style="left:741px;top:1577px"><svg width="34" height="34" viewBox="0 0 24 24" fill="none" stroke="#fff" stroke-width="1.6"><circle cx="7" cy="7" r="2.5"/><circle cx="17" cy="7" r="2.5"/><path d="M3 17a4 4 0 0 1 8 0M13 17a4 4 0 0 1 8 0M4 21h16"/></svg></div>
  <div class="service-label" style="left:825px;top:1590px">LIFESTYLE<br>AIDE</div>

  <div class="service-node" style="left:865px;top:1703px"><svg width="34" height="34" viewBox="0 0 24 24" fill="none" stroke="#fff" stroke-width="1.6"><path d="M3 11 12 3l9 8v10H3z"/><path d="M12 11v7M8.5 14.5h7"/></svg></div>
  <div class="service-label" style="left:950px;top:1716px">HOSPICE<br>AT HOME</div>

  <div class="service-node" style="left:913px;top:1844px"><svg width="34" height="34" viewBox="0 0 24 24" fill="none" stroke="#fff" stroke-width="1.6"><path d="M3 12h18v3a5 5 0 0 1-5 5H8a5 5 0 0 1-5-5zM6 12V5a2 2 0 0 1 4 0"/></svg></div>
  <div class="service-label" style="left:997px;top:1856px">BATHING &amp;<br>MEAL SERVICE</div>
</section>

<!-- senior living -->
<section class="senior">
  <div class="abs senior-bg"></div>
  <svg class="abs" style="left:0;top:2020px" width="1200" height="120" viewBox="0 0 1200 120" aria-hidden="true">
    <path d="M0 75 C350 -5 700 90 1200 15 L1200 120 L0 120Z" fill="#fdf6ee"/>
    <path d="M0 86 C250 20 500 30 700 70" stroke="#fff" stroke-width="10" fill="none"/>
    <path d="M380 60 C700 100 950 70 1200 10" stroke="var(--orange)" stroke-width="12" fill="none"/>
  </svg>
  <h2 class="heading abs" style="left:128px;top:2196px;font-size:46px">Senior Living</h2>
  <div class="rule" style="left:134px;top:2264px"></div>
  <p class="abs body-copy" style="left:128px;top:2290px;width:440px;font-size:18px;line-height:27.5px;color:#333">Marlow Senior Living creates a warm, supportive, and enriching care home environment where seniors can thrive in their golden years. We provide residential care that promotes well-being, connection, and dignity of each individual.</p>
  <div class="check-item" style="top:2442px">LONG-TERM STAY</div>
  <div class="check-item" style="top:2477px">SHORT-TERM STAY</div>
  <div class="btn btn-teal" style="left:123px;top:2530px;width:186px;height:50px;">LEARN MORE &#8250;</div>

  <div class="photo" style="left:594px;top:2252px;width:254px;height:318px;background:linear-gradient(160deg,#8a4a3a,#c8a46a 40%,#6a4a6e 75%,#d7c7a2)" role="img" aria-label="Three senior women laughing together on a sofa">
    <div class="tile-caption"><span>LONG TERM SAY</span><span class="tile-arrow">&#8250;</span></div>
  </div>
  <div class="photo" style="left:861px;top:2196px;width:254px;height:318px;background:linear-gradient(160deg,#e7e3c5,#8e5b3a 45%,#b8322f 70%,#d9c6a3)" role="img" aria-label="Caregiver serving a meal to seniors at a dining table">
    <div class="tile-caption"><span>SHORT TERM STAY</span><span class="tile-arrow">&#8250;</span></div>
  </div>
</section>

<!-- testimonials -->
<section class="testimonials">
  <h2 class="heading abs" style="left:0;width:1200px;text-align:center;top:2760px;font-size:40px;font-weight:600;color:#111">TESTIMONIALS</h2>
  <div class="rule" style="left:574px;top:2817px"></div>
  <div class="abs" style="left:86px;top:3040px;width:90px;height:140px;background:linear-gradient(160deg,#6c9a3a,#b9d27a);opacity:.45;border-radius:0 80px 0 0" role="img" aria-label="Palm frond accent"></div>
  <div class="abs" style="left:1060px;top:2870px;width:100px;height:140px;background:linear-gradient(200deg,#6c9a3a,#b9d27a);opacity:.45;border-radius:80px 0 0 0" role="img" aria-label="Palm frond accent"></div>
  <div class="testimonial" style="left:153px;top:2865px">
    <p>"Lorem ipsum dolor sit amet, consectetur adipiscing elit, sed do eiusmod tempor incididunt ut labore et dolore magna aliqua. Quis ipsum suspendisse ultrices gravida. Risus commodo viverra maecena"</p>
    <div class="reviewer">Kai Renner</div><div class="stars">&#9733;&#9733;&#9733;&#9733;&#9733;</div>
    <div class="quote-mark">&#8221;</div>
  </div>
  <div class="testimonial" style="left:626px;top:2865px">
    <p>"Lorem ipsum dolor sit amet, consectetur adipiscing elit, sed do eiusmod tempor incididunt ut labore et dolore magna aliqua. Quis ipsum suspendisse ultrices gravida. Risus commodo viverra maecena"</p>
    <div class="reviewer">Kai Renner</div><div class="stars">&#9733;&#9733;&#9733;&#9733;&#9733;</div>
    <div class="quote-mark">&#8221;</div>
  </div>
</section>

<!-- schedule -->
<section class="schedule">
  <div class="abs schedule-band" role="img" aria-label="Warm orange sunset with soft palm tree silhouettes"></div>
  <h2 class="heading">Schedule a Care<br>Consultation</h2>
  <div class="rule" style="left:112px;top:3418px;background:#fff"></div>
  <div class="field" style="left:110px;top:3457px;width:239px">First Name</div>
  <div class="field" style="left:358px;top:3457px;width:236px">Last Name</div>
  <div class="field" style="left:110px;top:3511px;width:239px">Email address</div>
  <div class="field" style="left:358px;top:3511px;width:236px">Phone Number</div>
  <div class="field" style="left:110px;top:3566px;width:484px;height:98px">Message</div>
  <div class="btn btn-teal" style="left:112px;top:3678px;width:196px;height:46px;">SEND MESSAGE</div>
  <div class="photo consult-photo" role="img" aria-label="Seniors exercising with dumbbells guided by a trainer"></div>
  <svg class="abs" style="left:0;top:3760px" width="1200" height="140" viewBox="0 0 1200 140" aria-hidden="true">
    <path d="M0 80 C300 10 700 120 1200 20 L1200 140 L0 140Z" fill="#fff"/>
    <path d="M0 95 C250 40 500 50 700 85" stroke="var(--teal)" stroke-width="10" fill="none"/>
    <path d="M380 70 C700 120 950 95 1200 25" stroke="var(--orange)" stroke-width="14" fill="none"/>
  </svg>
</section>

<!-- footer -->
<footer class="site-footer">
  <div class="abs" style="left:120px;top:3950px;display:flex;align-items:center;gap:10px"><div class="brand-mark" style="width:48px;height:48px"></div><div class="brand-name" style="font-size:20px">Marlow Health<br>Collective</div></div>
  <div class="btn btn-teal" style="left:130px;top:4030px;width:182px;height:36px;border-radius:0;font-size:12px;">LEARN</div>
  <div class="btn" style="left:130px;top:4083px;width:182px;height:36px;border-radius:0;font-size:12px;background:var(--orange-soft)">CARE GIVER JOBS</div>
  <div class="social" style="left:155px;border-color:var(--orange)"></div>
  <div class="social" style="left:193px"></div>
  <div class="social" style="left:231px"></div>
  <div class="social" style="left:269px"></div>

  <div class="abs footer-col" style="left:378px;top:3942px">
    <h3>Navigation</h3>
    <ul><li>Home Care</li><li>Senior Living</li><li>Rates</li><li>About Us</li></ul>
  </div>
  <div class="abs footer-col" style="left:586px;top:3942px">
    <h3>Services</h3>
    <ul><li>Nurse Aide Care</li><li>24-Hour Home Care</li><li>Skilled Nursing</li><li>Lifestyle Aide</li><li>Hospice at Home</li><li>Bathing &amp; Meal Service</li></ul>
  </div>
  <div class="abs footer-col" style="left:818px;top:3942px">
    <h3>Contact Us</h3>
  </div>
  <svg class="abs" style="left:832px;top:3990px" width="30" height="30" viewBox="0 0 24 24" aria-hidden="true"><path fill="var(--teal)" d="M12 2a7 7 0 0 0-7 7c0 5 7 13 7 13s7-8 7-13a7 7 0 0 0-7-7zm0 9.5A2.5 2.5 0 1 1 12 6.5a2.5 2.5 0 0 1 0 5z"/></svg>
  <div class="abs" style="left:876px;top:3986px;font-size:15px;line-height:18px;color:#333">248 Pueo Lane, Suite 310,<br>Honolulu, HI 96817</div>
  <div class="abs" style="left:832px;top:4040px;width:30px;height:30px;border-radius:50%;background:var(--teal);display:flex;align-items:center;justify-content:center"><svg width="15" height="15" viewBox="0 0 24 24"><path fill="#fff" d="M6.6 10.8a15 15 0 0 0 6.6 6.6l2.2-2.2c.3-.3.7-.4 1-.2 1.1.4 2.3.6 3.6.6.6 0 1 .4 1 1V20c0 .6-.4 1-1 1A17 17 0 0 1 3 4c0-.6.4-1 1-1h3.5c.6 0 1 .4 1 1 0 1.3.2 2.5.6 3.6.1.3 0 .7-.2 1z"/></svg></div>
  <div class="abs" style="left:876px;top:4036px;font-size:15px;line-height:18px;color:#333">Phone number<br><b style="font-family:Montserrat,sans-serif;font-size:17px">808-555-0172</b></div>

  <div class="abs" style="left:830px;top:4112px;width:110px;text-align:center;font-size:20px;font-weight:600;color:var(--teal-dark);line-height:22px"><div style="width:28px;height:28px;margin:0 auto 8px;border-radius:50%;background:var(--orange)"></div>Marlow<br>Homecare</div>
  <div class="abs" style="left:960px;top:4112px;width:130px;text-align:center;font-size:20px;font-weight:600;color:var(--teal-dark);line-height:22px"><div style="width:28px;height:28px;margin:0 auto 8px;border-radius:50%;background:var(--teal)"></div>Marlow<br>Senior Living</div>

  <div class="abs" style="left:0;top:4248px;width:1200px;height:1px;background:#e5e5e5"></div>
  <div class="copyright">Copyright &copy; 2024 <u>Marlow Health Collective</u>. All Right Reserved</div>
</footer>

</body>
</html>
```